Award-winnning Estate Agent needs a premium version of their 'For Sale' board design

We need a premium option for our 'For Sale' board design. We have a standard board that is attached to this brief, but were are looking to have a premium design version that we will use when selling exclusive properties. Our company name is Harbourline Vale Estates and the name for this is exclusive selection is: 'The Harbourline Collection'. The design needs to work with our current brand, but have a distinctive PREMIUM feel to it. I have uploaded the barnd guidelines and also some of the exisisting logo variations. We do NOT need a new logo but feel free to play around with colours, fonts, sizes etc. for the sign.

Target Market(s)

Property buyers & house hunters

Industry/Entity Type

Real Estate - Residential Property

Font styles to use
Sans Serif

Requirements
Must have
• A premium fee, must be square design, must be easy to read when driving past the sign
Nice to have
• I'm open ot ideas

```html
<!DOCTYPE html>
<html lang="en">
<head>
<meta charset="utf-8">
<title>For Sale Board – The Harbourline Collection</title>
<link rel="stylesheet" href="https://fonts.googleapis.com/css2?family=Raleway:wght@500;600;700&display=swap">
<style>
  :root {
    --navy: #173560;
    --gold: #bf914f;
    --white: #ffffff;
    --board-w: 1200px;
    --board-h: 1199px;
  }
  * { margin: 0; padding: 0; box-sizing: border-box; }
  html, body {
    width: var(--board-w);
    height: var(--board-h);
    overflow: hidden;
    background: var(--white);
  }
  .sale-board {
    position: relative;
    width: var(--board-w);
    height: var(--board-h);
    background: var(--white);
    font-family: "Raleway", sans-serif;
    color: var(--navy);
  }
  .board-headline {
    position: absolute;
    left: 114px;
    top: 104px;
    font-weight: 600;
    font-size: 156px;
    line-height: 146px;
    letter-spacing: 1px;
  }
  .headline-rule {
    position: absolute;
    left: 118px;
    top: 449px;
    width: 205px;
    height: 17px;
    background: var(--gold);
  }
  .board-phone {
    position: absolute;
    left: 116px;
    top: 518px;
    font-weight: 700;
    font-size: 80px;
    line-height: 1;
    letter-spacing: 1px;
  }
  .board-web {
    position: absolute;
    left: 118px;
    top: 612px;
    font-weight: 600;
    font-size: 27px;
    letter-spacing: 2.6px;
  }
  .brand-band {
    position: absolute;
    left: 0;
    top: 769px;
    width: 100%;
    height: 27px;
    background: var(--gold);
  }
  .brand-panel {
    position: absolute;
    left: 0;
    top: 796px;
    width: 100%;
    height: 403px;
    background: var(--navy);
    display: flex;
    align-items: center;
    justify-content: center;
  }
  .brand-name {
    color: var(--white);
    font-weight: 700;
    font-size: 52px;
    line-height: 1.2;
    letter-spacing: 2px;
    text-align: center;
    text-transform: uppercase;
  }
</style>
</head>
<body>
  <main class="sale-board">
    <h1 class="board-headline">FOR<br>SALE</h1>
    <div class="headline-rule"></div>
    <p class="board-phone">01632 960418</p>
    <p class="board-web">www.harbourlinevaleestates.co.uk</p>
    <div class="brand-band"></div>
    <section class="brand-panel">
      <p class="brand-name">The Harbourline<br>Collection</p>
    </section>
  </main>
</body>
</html>
```